Talvoro Web Design

We need a redesign of our current website www.talvoro-example.com

THIS IS A DESIGN STAGE ONLY

We have attached details of the whole project for your understanding only

We do not want to change our Logo but do want to have a more modern and intuitive feel to the site.

The first stage is the design but we are also looking for a coder to take the site to the next level

Talvoro has a current website that has been in operation for the past 6 years the design was based around the Saas self-service model and while functional does not meet Talvoro needs with regard to the new positioning.

We are happy to stay in Joomla or will look at alternatives

The purpose of the redesign is to align the look and feel of the website to meet our current new brand position and to provide a access point for the delivery of new content from Blogs and white papers as well as a portal for information for our current users for gathering Tips and Tricks and access to additional resources to assist them to provide feedback and get support.

Talvoro is Australia's only PPM (Project and Portfolio Management) software provider that caters to the needs of project managers and C-level executives looking for insights into the alignment of resources to business strategy and investment decisions.

As companies gain maturity in PPM there is a need for innovation and management of change beyond just implementation of tools this is why Talvoro has evolved from being a SaaS to becoming a SwS (Software with Service) provider.

Talvoro is recognized as the tool of choice amongst program and project managers that is able to provide the user with an intuitive reliable interface that is capable of evolving and maturing to meet and exceed client requirements.

We are able to provide people at the coalface with tools that enable them to manage resources, scope, time sheeting, issues, changes and risk with excellent reporting functionality.

For C-level executives we are able to provide Business Intelligence (BI) functionality and reporting by integrating the PPM data with other business management systems such as ERP and CRM to provide a insight beyond pure PPM reporting.

We are able to provide Project Management insights from years of experience working with our clients in developing solutions that are inline with the evolution that comes with change.

Please feel free to email me on marcus.hale@talvoro-example.com if you require any further details. A Site map and a wire frame is available.

Competitor sites include

www.plenvix-example.com
www.corbelo-example.com
www.quandrit-example.com
www.vestrel-example.com
Updates

Hi All 

We are getting some great designs coming in and really appreciate all of your efforts.

Some feedback to you all is that we have a preference for cleaner designs that take into account comprehension ability. So reverse type to us looks good but doesnt always get the cut through.

We have to remember that this is a marketing site first and foremost so what we are looking for is the ability to engage with our audience and get them to start to explore. That is upto us to provide great content and what we want from the design is the ability to be be able to engage with our Audience.

For your consideration please review this info from our marketing plan

There are 3 main communication groups inthe sales process.

Users-        These are the peoplewho will be at the coal face inputting the data and using the product on adaily basis. It is key to provide them with an easy to use and functional toolthat is able to provide them with the information they are looking for easily andintuitively. They have the capacity to say yes and can push the sale decisionup the chain. They equally have the power to say No and stop the sales processin its tracks. They will have a opinion who or what they feel is the best ofbreed and will try to influence the process.

Users are split into two groups.

Group1- They will be diploma if not degree qualifiedwill be a mix of Male and female with majority aged 18 to 35 they are at thecareer development stage of their life cycle normally on an income 45k to 70kper annum. We would position these people very strongly in the “What is in itfor me”.

Group2- PM who has used a variety of tools and systemsover the years they will be pre disposed to one or more systems and has morethan likely been exposed to MSP. Usually in the 30 to 50 year old age rangewith extensive on the job experience.

KeyInfluencers- These are the people who while notactually utilizing the software need to receive information in the form ofreports etc from the system. They normally don’t have the capacity to say yesbut they most certainly can say no. They will have come from a PM or IT roleand have a strong understanding of the PM processes. Influencers will be 30 to50 years of age they are at the family development stage with strong demandsfrom work and family predominantly male but not exclusively. They would bedegree qualified and possibly have completed or looking at additional studies. Therewill be an emphasis on getting the job done right. They are very time poor and hardto communicate with and engage. While being time poor they have an affinitywith and understand the greater good.

DecisionMakers- These are our key decision makers whilethey may not have direct input into the system or processes they are at the endof the day the people who approve the expenditure.

There is a huge demand for this person’stime with a multitude of people from internal employees and management,suppliers, customers, the community and potential suppliers. They are oftentravelling and going from one subject matter to another meeting after meeting.They will be at the stage where children are gaining some independents or leftthe home, career is stabilized and a clear path is formed. They are very directand deal in the facts and figures when it comes to decision making, they arenormally highly educated to the MBA or Doctorate level. They will be driven byoutcomes not the process of getting there.

 

A consistent theme across this group isthe following.

Psychographics

·Values time and considers ittheir single most limited resource.

·Excited about accepting andusing innovative ideas and products always wants to be at the fore front.

·Value adding has priority overprice

·Consistent web users: preferinternet over magazines and newspapers

Behavior

·They are leaders in productselection and respond to the opinions of the ‘Industry Experts’ when makingpurchase decisions.

·This group will look to theinternet to acquire the information

·Will make an informed decisionto purchase after due consideration.

·This group can be a powerfulsales force resulting from the referral network they build and use

Hope this helps

Hi All

Sorry for the delay we are in the final stages of decisions, so sorry we have had people away from the office who need to be involved in the process.

We will submit individual questions to those in the running and let all of the people who didnt get through this time as to why shortly.

We would like to thank you all for your efforts and submissions.

Regards

Marcus Hale 

Industry/Entity Type

Business Management

Requirements
Must have
• The scope of the website is to provide a modern functional website that is easy to navigate and provides a range of products and services to meet the needs of our potential clients and current users.

Two potential groups of viewers exist:
1. Potential Clients and users from the Project management community these would be split into 3 distinct groups. ( Please refer to Page 20 Talvoro marketing Plan)
a. Project Managers
b. Project Directors
c. Business Managers
2. Current Talvoro Users

The goal of website is to engage with the project management community reinforcing the Talvoro Brand as Software with Service the key ethos should be around the company being thought leaders and industry experts with a strong commitment to clients and the success of their Portfolio/Program Management Office

Maintaining a modern and user friendly site is of the highest importance in order to hold users attention and guide the viewer to information that will lead to a decision to pursue accreditation and association with the Talvoro Brand

We would like to guide potential clients to want to engage with us in assisting them to understand their current position in the P3M3 maturity model and to use us as a source for information and guidance.

Benefits for using the site should include:
• Information from a broad spectrum of Project Management professionals and recognized industry experts.
• Information on the Talvoro Product and Services
• Timely and up to date information that encourages readers to return to the site
• Call to action, and plans for potential users of Talvoro software.
• Demonstrate the benefits of accreditation and Call to action for current users to gain accreditation.
• Call to action for attending monthly webinars
• Ability to review past webinars, whitepapers etc.

```html
<!DOCTYPE html>
<html lang="en">
<head>
<meta charset="utf-8">
<title>Talvoro – Project Management Software</title>
<link rel="stylesheet" href="https://fonts.googleapis.com/css2?family=Arimo:ital,wght@0,400;0,700;1,400&display=swap">
<style>
:root{
  --ink:#333;
  --muted:#555;
  --orange:#f26a1b;
  --orange-light:#ff8a3a;
  --red:#e8401c;
  --dark:#1c1c1c;
  --charcoal:#2f2f2f;
  --footer:#333;
  --card:#fff;
  --line:#dcdcdc;
  --hero-text:#b7bfcc;
}
*{margin:0;padding:0;box-sizing:border-box}
html,body{width:1000px;height:1200px;overflow:hidden}
body{font-family:"Arimo",Arial,sans-serif;color:var(--ink);background:#fff;position:relative}
a{color:inherit;text-decoration:none}

.top-bar{position:absolute;left:0;top:0;width:1000px;height:84px;background:linear-gradient(#3a3a3a,#0c0c0c 60%,#000);border-top:2px solid #555}
.brand{position:absolute;left:75px;top:22px;display:flex;align-items:center;gap:8px;color:#fff;font-size:38px;font-weight:400;letter-spacing:-0.5px}
.brand-dot{width:12px;height:12px;border-radius:50%;background:var(--orange)}
.top-links{position:absolute;right:75px;top:33px;display:flex;gap:39px;font-size:14px;color:#fff}
.top-links .active{color:var(--orange-light)}

.main-nav{position:absolute;left:0;top:84px;width:1000px;height:46px;background:linear-gradient(#ff7a33,#e84a12)}
.main-nav ul{list-style:none;display:flex;position:absolute;left:75px;top:0;height:46px;border-left:1px solid #c9400f}
.main-nav li{height:46px;line-height:46px;padding:0 20px;color:#fff;font-size:12.5px;font-weight:700;border-right:1px solid #c9400f;box-shadow:inset 1px 0 0 #ff965e}
.main-nav li.current{background:#e3410c}

.hero{position:absolute;left:0;top:130px;width:1000px;height:250px;background:linear-gradient(#2e2e2e,#3b3b3b);border-bottom:3px solid #fff}
.hero-art{position:absolute;left:155px;top:18px;width:185px;height:205px;border-radius:8px;background:linear-gradient(135deg,#ff7a2a 0%,#e2561c 35%,#b9c1cf 55%,#6f7a8f 100%);opacity:.9}
.hero-title{position:absolute;left:406px;top:46px;color:var(--hero-text);font-size:36px;font-weight:700;letter-spacing:.5px}
.hero-sub{position:absolute;left:407px;top:90px;color:#a9aeb7;font-size:17.5px;font-weight:700}
.btn-know{position:absolute;left:711px;top:126px;width:112px;height:35px;border-radius:3px;background:linear-gradient(#ffa24a,#f57a16);color:#3a1a05;font-size:14px;font-weight:700;text-align:center;line-height:35px}
.dots{position:absolute;left:832px;top:216px;display:flex;gap:15px}
.dots span{width:12px;height:12px;border-radius:50%;background:#8b8b8b;box-shadow:inset 0 1px 2px #333}
.dots span.on{background:#fff;box-shadow:0 2px 0 #999}

.features{position:absolute;left:0;top:383px;width:1000px;height:260px;background:linear-gradient(#e4e4e4,#fff 60%)}
.feature-card{position:absolute;top:18px;width:202px;height:174px;background:var(--card);border:1px solid #e2e2e2;box-shadow:0 0 4px rgba(0,0,0,.08);text-align:center}
.feature-icon{position:absolute;left:14px;top:14px;width:46px;height:46px;border-radius:4px}
.feature-title{position:absolute;left:76px;top:18px;text-align:left;color:var(--red);font-size:15.5px;font-weight:700;line-height:18px}
.feature-title.single{top:27px}
.feature-text{position:absolute;left:12px;right:12px;top:73px;font-size:11.5px;line-height:17.5px;color:#444}
.btn-download{position:absolute;top:200px;width:159px;height:31px;border-radius:2px;background:linear-gradient(#5a5a5a,#2a2a2a);color:#fff;font-size:13px;font-weight:700;text-align:center;line-height:31px;letter-spacing:.2px}

.divider{position:absolute;left:75px;width:850px;height:1px;background:var(--line)}

.welcome-title{position:absolute;left:76px;top:668px;color:var(--red);font-size:17.5px;font-weight:700}
.welcome-text{position:absolute;left:75px;top:702px;width:616px;font-size:11.3px;line-height:19px;color:#444}
.welcome-text p{margin-bottom:7px}
.product-shot{position:absolute;left:733px;top:671px;width:177px;height:155px;border-radius:4px;background:linear-gradient(#1a1a1a 0 75%,#c9c9c9 75%,#9a9a9a)}

.testimonials{position:absolute;left:75px;top:852px;width:850px;height:161px;background:#f6f6f6;border:1px solid #d6d6d6;border-radius:2px}
.testimonials h2{position:absolute;left:0;width:100%;top:17px;text-align:center;font-size:14px;font-weight:700;color:#333}
.quote{position:absolute;top:58px;width:235px;font-size:12.4px;line-height:19px;font-style:italic;color:#666}
.quote-by{position:absolute;top:126px;font-size:11.5px;color:#333}
.quote-by b{font-weight:400;color:var(--red);font-size:13px}
.quote-rule{position:absolute;top:60px;width:1px;height:86px;background:#ccc}

.site-footer{position:absolute;left:0;top:1026px;width:1000px;height:174px;background:var(--footer)}
.foot-links{position:absolute;top:20px;list-style:none;font-size:11px;line-height:21px;color:#e6e6e6}
.foot-rule{position:absolute;top:17px;width:1px;height:75px;background:#555}
.signup-title{position:absolute;left:451px;top:24px;color:var(--orange-light);font-size:15px}
.signup{position:absolute;left:451px;top:49px;width:191px;height:29px;border:1px solid #bbb;background:#fff}
.signup span{position:absolute;left:13px;top:8px;font-size:10.5px;color:#444}
.signup b{position:absolute;right:1px;top:1px;width:60px;height:25px;background:#2a2a2a;color:#fff;font-size:13px;line-height:25px;text-align:center}
.btn-trial{position:absolute;left:717px;top:17px;width:194px;height:31px;border-radius:3px;background:linear-gradient(#ffa24a,#f57a16);color:#2d1404;font-size:13px;font-weight:700;text-align:center;line-height:31px}
.social{position:absolute;left:810px;top:60px;display:flex;gap:13px}
.social span{width:25px;height:25px;border-radius:3px;background:#6d7f96}
.foot-bottom-rule{position:absolute;left:75px;top:116px;width:850px;height:1px;background:#4a4a4a}
.copyright{position:absolute;left:0;width:100%;top:139px;text-align:center;font-size:11px;color:#ddd}
</style>
</head>
<body>

<header class="top-bar">
  <div class="brand"><span>talvoro</span><span class="brand-dot"></span></div>
  <nav class="top-links">
    <a class="active" href="#">Tour</a><a href="#">Features</a><a href="#">Pricing</a><a href="#">Sign up</a>
  </nav>
</header>

<nav class="main-nav">
  <ul>
    <li class="current">HOME</li><li>FAQ</li><li>DOWNLOAD</li><li>SUPPORT &amp; TRAINING</li><li>CUSTOMERS</li><li>ABOUT US</li><li>LOGIN</li><li>CONTACT US</li>
  </ul>
</nav>

<section class="hero">
  <div class="hero-art" role="img" aria-label="3D bar and pie chart illustration in orange and silver"></div>
  <h1 class="hero-title">PROJECT MANGEMENT</h1>
  <p class="hero-sub">Simple, easy to use project management software.</p>
  <a class="btn-know" href="#">KNOW MORE</a>
  <div class="dots"><span class="on"></span><span></span><span></span><span></span></div>
</section>

<section class="features">
  <div class="feature-card" style="left:75px">
    <div class="feature-icon" role="img" aria-label="Colourful project chart icon" style="background:linear-gradient(135deg,#e25b4b,#f5c842,#7cbf5a,#5b8fd6)"></div>
    <h3 class="feature-title">Project<br>Management</h3>
    <p class="feature-text">Simple, easy to use project man-agement software. Plan, Track and Improve your projects. Reduce costs and increase efficiency.</p>
  </div>
  <div class="feature-card" style="left:291px">
    <div class="feature-icon" role="img" aria-label="Calendar and clock icon" style="background:linear-gradient(#e9eef4,#b8c2cc)"></div>
    <h3 class="feature-title single">Timesheets</h3>
    <p class="feature-text">Powerful hosted project time and status collection. Track expenses and time. Have an audit trail on your time billing. Timesheet software</p>
  </div>
  <div class="feature-card" style="left:508px">
    <div class="feature-icon" role="img" aria-label="Filing cabinet icon" style="background:linear-gradient(#f0f0f0,#a9a9a9)"></div>
    <h3 class="feature-title">Resource<br>Management</h3>
    <p class="feature-text">Plan, manage and control work for your whole organisation or a single project. Resource man-agement</p>
  </div>
  <div class="feature-card" style="left:724px">
    <div class="feature-icon" role="img" aria-label="Clipboard report icon" style="background:linear-gradient(#f7e7b5,#e0b85a)"></div>
    <h3 class="feature-title">Issues, Risks<br>and change</h3>
    <p class="feature-text">Track and report on issues, risk and change. One click reports. issue management</p>
  </div>
  <a class="btn-download" href="#" style="left:96px">DOWNLOAD NOW</a>
  <a class="btn-download" href="#" style="left:313px">DOWNLOAD NOW</a>
  <a class="btn-download" href="#" style="left:530px">DOWNLOAD NOW</a>
  <a class="btn-download" href="#" style="left:746px">DOWNLOAD NOW</a>
</section>

<div class="divider" style="top:643px"></div>

<h2 class="welcome-title">Welcome to talvoro</h2>
<div class="welcome-text">
  <p>Nullam sagittis nisl at metus varius rhoncus. Quisque nec arcu hendrerit arcu pretium molestie vitae vel magna. Nam vitae dignissim ante. Ut vitae diam vel ipsum semper gravida sit amet tincidunt leo. Vestibulum sapien mi, imperdiet vehicula augue ac, faucibus porttitor justo. Cras a elementum lacus, sit amet ornare enim. Morbi euismod laoreet nunc rhoncus eleifend. Proin bibendum ultrices lectus id rhoncus. Nunc eleifend blandit eros malesuada gravida.</p>
  <p>Morbi dictum commodo ante, vel accumsan ante tincidunt sed. Aliquam sit amet nulla at quam adipiscing imperdiet. Duis iaculis sapien metus, eget feugiat mi ullamcorper sit amet.</p>
</div>
<div class="product-shot" role="img" aria-label="Desktop monitor showing the project schedule screen"></div>

<section class="testimonials">
  <h2>What our cutomer says</h2>
  <p class="quote" style="left:22px">“ Neque porro quisquam est, qui dolorem ipsum quia dolor sit amet incidunt ut labore etlarn dolore magnam aliquam. ”</p>
  <p class="quote-by" style="left:23px"><b>First Name</b> Title, Company</p>
  <div class="quote-rule" style="left:281px"></div>
  <p class="quote" style="left:312px">“ Neque porro quisquam est, qui dolorem ipsum quia dolor sit amet incidunt ut labore etlarn dolore magnam aliquam. ”</p>
  <p class="quote-by" style="left:313px"><b>First Name</b> Title, Company</p>
  <div class="quote-rule" style="left:571px"></div>
  <p class="quote" style="left:602px">“ Neque porro quisquam est, qui dolorem ipsum quia dolor sit amet incidunt ut labore etlarn dolore magnam aliquam. ”</p>
  <p class="quote-by" style="left:603px"><b>First Name</b> Title, Company</p>
</section>

<footer class="site-footer">
  <ul class="foot-links" style="left:86px"><li>Home</li><li>FAQ</li><li>Support &amp; Training</li><li>Contact Us</li></ul>
  <ul class="foot-links" style="left:223px"><li>Tour</li><li>Features</li><li>Pricing</li><li>Sign up</li></ul>
  <ul class="foot-links" style="left:313px"><li>Careers</li><li>Privacy Policy</li><li>Terms of Sale</li><li>Sitemap</li></ul>
  <div class="foot-rule" style="left:417px"></div>
  <p class="signup-title">Email Signup</p>
  <div class="signup"><span>Email ID</span><b>SUBMIT</b></div>
  <div class="foot-rule" style="left:677px"></div>
  <a class="btn-trial" href="#">GET A FREE TRIAL NOW</a>
  <div class="social"><span aria-label="Social link"></span><span aria-label="Social link"></span><span aria-label="Social link"></span></div>
  <div class="foot-bottom-rule"></div>
  <p class="copyright">Copyright &nbsp; © 2003 &nbsp;talvoro pty. ltd. All Rights Reserved</p>
</footer>

</body>
</html>
```